Communication and Marketing agency needs a new presentation card

We are a group of communication and marketing agencies specialized in companies that are in the logistics and industrial sector. The head agency is TELVANO Grupo and the group consists of 4 agencies: TELVANO Media, TELVANO Digital, TELVANO Research and DifundeEnPantalla. We hace 4 offices in Spain (Madrid, Barcelona, Valencia and Murcia). We are looking for a clean and attractive design that transmits our experience, brand presence in the market and knowledge to those who receive the card.It has to maintain the colors of the logo that is attached.
Target Market(s)
logistics and industrial sector
Marketing department
Contact Information for Business Card
Clean and attractive design

```html
<!DOCTYPE html>
<html lang="es">
<head>
<meta charset="utf-8">
<title>DifundeEnPantalla – Tarjeta de presentación</title>
<link rel="stylesheet" href="https://fonts.googleapis.com/css2?family=Roboto:ital,wght@0,400;1,400&display=swap">
<style>
  :root {
    --ink-dark: #2e2926;
    --brand-red: #b3202b;
    --paper-light: #f0f0f1;
    --paper-shade: #dcdcde;
    --ribbon-dark: #2b2725;
    --ribbon-fold: #5a5755;
    --text-light: #ffffff;
  }
  * { margin: 0; padding: 0; box-sizing: border-box; }
  html, body {
    width: 1200px;
    height: 686px;
    overflow: hidden;
    background: var(--ink-dark);
  }
  .business-card {
    position: relative;
    width: 1200px;
    height: 686px;
    overflow: hidden;
    background: var(--ink-dark);
    font-family: "Roboto", Arial, sans-serif;
    color: var(--text-light);
  }
  .card-shapes {
    position: absolute;
    inset: 0;
    width: 1200px;
    height: 686px;
  }
  .holder-name,
  .holder-role,
  .contact-line {
    position: absolute;
    font-style: italic;
    font-weight: 400;
    white-space: nowrap;
    line-height: 1;
  }
  .holder-name {
    left: 300px;
    top: 124px;
    transform: translateX(-50%);
    font-size: 43px;
    letter-spacing: 0.2px;
  }
  .holder-role {
    left: 300px;
    top: 176px;
    transform: translateX(-50%);
    font-size: 33px;
  }
  .contact-line { font-size: 28px; }
  .contact-phone   { left: 167px; top: 268px; }
  .contact-email   { left: 193px; top: 331px; }
  .contact-web     { left: 219px; top: 393px; }
  .contact-address { left: 246px; top: 455px; line-height: 40px; }
  .contact-address span { display: block; }
  .contact-address span + span { padding-left: 15px; }
  .brand-name {
    position: absolute;
    left: 894px;
    top: 342px;
    transform: translate(-50%, -50%);
    font-size: 50px;
    font-weight: 400;
    color: var(--brand-red);
    white-space: nowrap;
    letter-spacing: 0.5px;
  }
</style>
</head>
<body>
<main class="business-card">
  <svg class="card-shapes" viewBox="0 0 1200 686" aria-hidden="true">
    <defs>
      <linearGradient id="paper-gradient" x1="0" y1="0" x2="1" y2="1">
        <stop offset="0" stop-color="var(--paper-light)"/>
        <stop offset="1" stop-color="var(--paper-shade)"/>
      </linearGradient>
    </defs>
    <polygon class="red-band" points="0,0 459,0 753,686 0,686" fill="var(--brand-red)"/>
    <polygon class="paper-wedge" points="0,56 270,686 0,686" fill="url(#paper-gradient)"/>
    <polygon class="ribbon-fold" points="70,255 80,238 86,255" fill="var(--ribbon-fold)"/>
    <polygon class="ribbon-fold" points="214,581 224,585 218,595" fill="var(--ribbon-fold)"/>
    <polygon class="contact-ribbon" points="70,255 137,255 247,514 214,581" fill="var(--ribbon-dark)"/>

    <g class="icon-phone" fill="var(--text-light)">
      <rect x="119" y="279" width="15" height="26" rx="2.5" fill="none" stroke="var(--text-light)" stroke-width="2.2"/>
      <rect x="123" y="299" width="7" height="2" rx="1"/>
      <path d="M110 296 q0-6 6-7 l3 0 0 14 -4 0 q-5 0-5-7z"/>
      <path d="M130 293 h6 v12 q0 3-3 3 h-3z"/>
    </g>
    <g class="icon-mail" fill="none" stroke="var(--text-light)" stroke-width="1.8">
      <rect x="135" y="348" width="27" height="18" fill="var(--text-light)" stroke="none"/>
      <path d="M135 348 l13.5 10 13.5-10" stroke="var(--ribbon-dark)"/>
      <path d="M135 366 l10-8 M162 366 l-10-8" stroke="var(--ribbon-dark)" stroke-width="1.2"/>
    </g>
    <g class="icon-web">
      <circle cx="174" cy="422" r="12" fill="var(--text-light)"/>
      <rect x="161" y="417" width="26" height="9" fill="var(--ribbon-dark)"/>
      <text x="174" y="425" font-family="Roboto, Arial, sans-serif" font-size="8" font-weight="400" fill="var(--text-light)" text-anchor="middle">www</text>
    </g>
    <g class="icon-pin" fill="none" stroke="var(--text-light)" stroke-width="1.8">
      <path d="M200 484 c-6-7-8-10-8-14 a8 8 0 0 1 16 0 c0 4-2 7-8 14z"/>
      <circle cx="200" cy="470" r="2.8"/>
      <path d="M194 479 h-5 l-3 11 h28 l-3-11 h-5"/>
    </g>
  </svg>

  <h1 class="holder-name">LUCAS FERRANT</h1>
  <p class="holder-role">DIRECTOR</p>

  <p class="contact-line contact-phone">0612 48 30517</p>
  <p class="contact-line contact-email">info@difundeenpantalla.es</p>
  <p class="contact-line contact-web">www.difundeenpantalla.es</p>
  <p class="contact-line contact-address"><span>Calle Ribera 214, 3ºB,</span><span>46021 Valencia</span></p>

  <p class="brand-name">DifundeEnPantalla</p>
</main>
</body>
</html>
```